New Business Card Design Project

Need a design that will create an impact / strong impression towards our clients for our business. We are in the lighting business and we do lighting retrofits for large commercial to industrial clientele.

Target Market(s)

Lighting Industry

Industry/Entity Type

Business

Font styles to use
Other font styles liked:
• we would like to use the font on our logo, not sure what it is though..

Requirements
Must have
• Our logo.
Nice to have
• We are open to suggestions that have to do with lighting.

```html
<!DOCTYPE html>
<html lang="en">
<head>
<meta charset="utf-8">
<title>Kelvara Retrofit Group — Business Card</title>
<link rel="stylesheet" href="https://fonts.googleapis.com/css2?family=Lato:wght@400;700&display=swap">
<style>
  :root {
    --backdrop: #4b4b4b;
    --brand-green: #0a8237;
    --deep-green: #0b5a24;
    --paper: #ffffff;
    --ink: #1b1b1b;
  }
  * { box-sizing: border-box; margin: 0; padding: 0; }
  html, body { width: 1200px; height: 900px; overflow: hidden; }
  body {
    background: var(--backdrop);
    font-family: "Lato", Arial, sans-serif;
    position: relative;
  }
  .card {
    position: absolute;
    left: 250px;
    width: 700px;
    height: 400px;
    overflow: hidden;
    box-shadow: 0 6px 18px rgba(0,0,0,0.35);
  }
  .card-front { top: 35px; background: var(--brand-green); color: var(--paper); }
  .card-back { top: 465px; background: var(--paper); color: var(--ink); }

  .wordmark {
    position: absolute;
    display: flex;
    align-items: center;
    gap: 14px;
    font-weight: 700;
    white-space: nowrap;
  }
  .wordmark-square { width: 22px; height: 22px; flex: none; }
  .card-front .wordmark {
    left: 0; right: 0; top: 135px;
    justify-content: center;
    font-size: 46px;
  }
  .card-front .wordmark-square { background: var(--paper); }
  .website {
    position: absolute;
    left: 0; right: 0; top: 320px;
    text-align: center;
    font-size: 20px;
    letter-spacing: 1px;
  }

  .card-back .wordmark {
    left: 40px; top: 40px;
    font-size: 34px;
    color: var(--brand-green);
  }
  .card-back .wordmark-square { background: var(--brand-green); }

  .contact {
    position: absolute;
    left: 40px; top: 150px;
    font-size: 19px;
    line-height: 27px;
  }
  .contact-row { display: flex; align-items: center; gap: 10px; }
  .contact-row svg { width: 18px; height: 18px; flex: none; fill: var(--brand-green); }
  .address { padding-left: 28px; }

  .person {
    position: absolute;
    right: 50px; top: 200px;
    text-align: right;
  }
  .person-name { font-size: 32px; font-weight: 700; color: var(--brand-green); }
  .person-role { font-size: 20px; margin-top: 4px; }

  .band-stripe {
    position: absolute;
    left: 0; top: 318px;
    width: 560px; height: 14px;
    background: var(--brand-green);
  }
  .band-block {
    position: absolute;
    left: 610px; top: 340px;
    width: 90px; height: 30px;
    background: var(--brand-green);
  }
</style>
</head>
<body>
  <section class="card card-front">
    <div class="wordmark"><span class="wordmark-square"></span>Kelvara Retrofit Group</div>
    <p class="website">www.kelvara-group.com</p>
  </section>

  <section class="card card-back">
    <div class="wordmark"><span class="wordmark-square"></span>Kelvara Retrofit Group</div>

    <div class="contact">
      <p class="address">2140 North Alder Avenue</p>
      <p class="address">Brookfield, IL 60513</p>
      <p class="contact-row">
        <svg viewBox="0 0 24 24" aria-hidden="true"><path d="M6.6 10.8a15.1 15.1 0 0 0 6.6 6.6l2.2-2.2a1 1 0 0 1 1-.25 11.4 11.4 0 0 0 3.6.57 1 1 0 0 1 1 1V20a1 1 0 0 1-1 1A17 17 0 0 1 3 4a1 1 0 0 1 1-1h3.5a1 1 0 0 1 1 1c0 1.25.2 2.45.57 3.57a1 1 0 0 1-.25 1z"/></svg>
        (555) 214-7700
      </p>
      <p class="contact-row">
        <svg viewBox="0 0 24 24" aria-hidden="true"><path d="M7 3h10v4H7zM4 8h16a2 2 0 0 1 2 2v6h-4v5H6v-5H2v-6a2 2 0 0 1 2-2zm4 8v3h8v-3z"/></svg>
        (555) 214-7701
      </p>
      <p class="contact-row">
        <svg viewBox="0 0 24 24" aria-hidden="true"><path d="M2 5h20v14H2zm2 2v.5l8 5 8-5V7zm0 2.8V17h16V9.8l-8 5z"/></svg>
        hello@kelvara-group.com
      </p>
    </div>

    <div class="person">
      <p class="person-name">Marcus Ellery</p>
      <p class="person-role">Manager</p>
    </div>

    <div class="band-stripe"></div>
    <div class="band-block"></div>
  </section>
</body>
</html>
```